Swing Dance Themed Cleaning Company Website

We need a website designed for a cleaning company based in Portland, Oregon called Foxtrot Lane. We clean homes and commercial buildings, inside and out.

needs to be vintage and like the velvet tambour. Speakeasy 1920s feel.
needs to be classy.

Check out foxtrotlane.com We are not happy with the site currently.

please look at house scout site for more content https://www.housescoutpro.com/rated.FoxtrotLaneCleaning.48217705.html

Check out my videos on my ClipHaven channel Foxtrot Lane

Target Market(s)

middle class and home owner

Industry/Entity Type

Cleaning Service

Number of Pages Required

3 page

Font styles to use
Other font styles liked:
• jazzrag

Colors

Designer to choose colors to be used in the design.

Requirements
Must have
• must be good on pc and mobile

```html
<!DOCTYPE html>
<html lang="en">
<head>
<meta charset="utf-8">
<title>Foxtrot Lane — Commercial and Residential Cleaning</title>
<link href="https://fonts.googleapis.com/css2?family=Poiret+One&family=Open+Sans:wght@400;600;700;800&family=Roboto:wght@400;500&display=swap" rel="stylesheet">
<style>
:root{
  --yellow:#f7e500;
  --yellow-deep:#f2c500;
  --ink:#111111;
  --charcoal:#2a2a2a;
  --card:#1c1c1c;
  --paper:#ebe5d9;
  --paper-dark:#d9cfbd;
  --brown-dark:#4a2a12;
  --brown-mid:#8a5a2b;
  --brown-light:#b07a3e;
  --text:#3a3a3a;
  --muted:#8a8a8a;
  --white:#ffffff;
  --field:#4a4410;
}
*{margin:0;padding:0;box-sizing:border-box}
html,body{width:1200px;height:2866px;overflow:hidden}
body{position:relative;background:var(--ink);font-family:'Open Sans',sans-serif;color:var(--text)}
.deco{font-family:'Poiret One',cursive;font-weight:400;text-transform:uppercase}
section,header,footer{position:absolute;left:0;width:1200px}
.abs{position:absolute}

/* hero */
.hero{top:0;height:660px;background:radial-gradient(ellipse at 30% 40%,var(--brown-light) 0%,var(--brown-mid) 45%,var(--brown-dark) 100%)}
.brand{left:185px;top:24px;display:flex;align-items:center;gap:10px}
.brand-mark{width:34px;height:34px;background:var(--yellow)}
.brand-name{font-family:'Open Sans',sans-serif;font-weight:800;font-size:27px;line-height:27px;color:var(--yellow);text-transform:uppercase;width:170px}
.tagline{left:185px;top:88px;font-size:11px;color:var(--yellow);text-transform:uppercase;letter-spacing:.3px}
.nav{left:488px;top:32px;display:flex;align-items:center}
.nav a{font-family:'Poiret One',cursive;text-transform:uppercase;color:var(--white);text-decoration:none;font-size:15px;font-weight:700;padding:8px 0;margin-right:64px}
.nav a.active{background:#2b2118;padding:8px 26px;margin-right:36px}
.hero-title{left:178px;top:212px;font-size:44px;line-height:38px;color:var(--white)}
.btn{display:inline-block;background:var(--yellow);color:var(--ink);font-family:'Poiret One',cursive;font-weight:700;text-transform:uppercase;font-size:17px;text-align:center}
.hero-btn{left:178px;top:355px;width:152px;height:46px;line-height:46px}
.slider{left:182px;top:428px;display:flex;align-items:center;gap:6px}
.slider .arrow{width:18px;height:18px;border-radius:50%;background:var(--white)}
.slider .dot{width:7px;height:7px;border-radius:50%;background:#cfc4b4}
.slider .dot.on{background:var(--white)}
.hero-photo{left:500px;top:110px;width:700px;height:560px;background:linear-gradient(160deg,#c98a6a 0%,#6fa86a 55%,#3f7a48 100%);border-radius:220px 220px 0 0}

/* about */
.about{top:630px;height:580px;background:var(--paper)}
.about-art{left:150px;top:110px;width:420px;height:340px;background:radial-gradient(ellipse,#cfc7b8 0%,var(--paper) 70%)}
.about-title{left:588px;top:122px;font-size:38px;line-height:36px;color:var(--ink)}
.about-lead{left:588px;top:218px;font-size:14px}
.about-sub{left:588px;top:246px;font-size:18px;font-weight:600;color:var(--ink)}
.about-text{left:588px;top:282px;width:440px;font-size:14px;line-height:22px}
.about-btn{left:585px;top:372px;width:150px;height:44px;line-height:44px}

/* services */
.services{top:1195px;height:540px;background:radial-gradient(ellipse at center,#3a3a3a 0%,var(--charcoal) 60%,#1a1a1a 100%)}
.section-title{left:0;width:1164px;text-align:center;font-size:32px}
.services .section-title{top:70px;color:var(--yellow)}
.card{width:202px;height:256px;background:var(--card);border-radius:6px;text-align:center;padding:22px 16px 0}
.icon{width:92px;height:92px;border-radius:50%;background:var(--yellow);margin:0 auto 16px;display:flex;align-items:center;justify-content:center}
.card h3{font-family:'Poiret One',cursive;text-transform:uppercase;color:var(--white);font-size:17px;line-height:18px;font-weight:700;margin-bottom:8px}
.card p{font-size:11px;line-height:16px;color:#bdbdbd}

/* blogs */
.blogs{top:1725px;height:510px;background:linear-gradient(180deg,var(--paper) 0%,var(--paper-dark) 100%)}
.blogs .section-title{top:80px;color:var(--ink)}
.post{width:262px;top:152px}
.post-photo{width:262px;height:154px}
.date{position:absolute;left:22px;top:140px;width:100px;height:26px;line-height:26px;background:var(--yellow);color:var(--ink);font-size:13px;text-align:center}
.post h4{margin-top:28px;font-size:14px;line-height:17px;font-weight:700;color:var(--ink)}
.post p{margin-top:12px;font-size:10px;line-height:15px;color:var(--muted)}
.post .more{margin-top:6px;font-size:13px;font-weight:700;color:var(--ink);text-transform:uppercase}

/* contact */
.contact{top:2230px;height:500px;background:linear-gradient(180deg,var(--yellow-deep) 0%,var(--yellow) 60%,#f4e800 100%)}
.contact .section-title{top:42px;color:var(--ink)}
.contact-intro{left:183px;top:120px;width:320px;font-family:'Roboto',sans-serif;font-size:16px;line-height:22px;color:var(--ink)}
.info{left:183px;display:flex;gap:14px;font-family:'Roboto',sans-serif;font-size:14px;line-height:22px;color:var(--ink)}
.info b{font-weight:500;text-transform:uppercase;display:block}
.field{background:var(--field);color:#e9e4b0;font-family:'Roboto',sans-serif;font-size:14px;padding:0 14px;line-height:38px;height:38px}
.submit{left:550px;top:332px;width:148px;height:46px;line-height:46px;background:var(--ink);color:var(--white);font-family:'Poiret One',cursive;font-weight:700;font-size:20px;text-align:center;text-transform:uppercase}

/* footer */
.footer{top:2715px;height:151px;background:var(--ink)}
.foot-nav{left:183px;top:60px;display:flex;gap:46px}
.foot-nav a{font-family:'Poiret One',cursive;font-weight:700;text-transform:uppercase;color:var(--white);text-decoration:none;font-size:15px}
.copy{left:183px;top:92px;font-size:11px;color:#bbbbbb}
.social{left:874px;top:52px;display:flex;gap:8px}
.social span{width:30px;height:30px;border-radius:50%;background:var(--white)}
.edge{position:absolute;left:0;width:1200px}
</style>
</head>
<body>

<header class="hero">
  <div class="abs hero-photo" role="img" aria-label="Photo of a retro-styled cleaning woman in a green striped dress holding a yellow cloth and spray bottle"></div>
  <div class="abs brand"><span class="brand-mark"></span><span class="brand-name">Foxtrot Lane</span></div>
  <div class="abs tagline">Keep cleaning classy Portland</div>
  <nav class="abs nav">
    <a class="active" href="#">Home</a><a href="#">About Us</a><a href="#">Services</a><a href="#">Blogs</a><a href="#">Contact Us</a>
  </nav>
  <h1 class="abs hero-title deco">Commercial<br>and Residential<br>Cleaning</h1>
  <a class="abs btn hero-btn" href="#">View Services</a>
  <div class="abs slider"><span class="arrow"></span><span class="dot on"></span><span class="dot"></span><span class="dot"></span><span class="dot"></span><span class="arrow"></span></div>
</header>

<section class="about">
  <svg class="edge" style="top:-24px" height="40" viewBox="0 0 1200 40" preserveAspectRatio="none"><polygon fill="#ebe5d9" points="0,22 60,14 130,26 210,10 290,24 370,12 450,28 540,16 620,30 700,12 790,26 870,14 950,28 1030,10 1110,24 1200,8 1200,40 0,40"/></svg>
  <div class="abs about-art" role="img" aria-label="Sketch of a dapper man in a suit dancing with a mop"></div>
  <h2 class="abs about-title deco">About<br>Foxtrot Lane</h2>
  <p class="abs about-lead">Making the greater Portland area clean, one building at a time</p>
  <p class="abs about-sub">Good people, great service</p>
  <p class="abs about-text">Foxtrot Lane is a family owned professional cleaning business. We provide our years of cleaning experience to homes and businesses in and around Portland, Oregon.</p>
  <a class="abs btn about-btn" href="#">Read More</a>
</section>

<section class="services">
  <svg class="edge" style="top:-18px" height="36" viewBox="0 0 1200 36" preserveAspectRatio="none"><polygon fill="#2a2a2a" points="0,18 80,8 160,20 250,6 330,22 420,10 500,24 590,8 680,22 760,6 850,20 940,10 1020,24 1110,8 1200,18 1200,36 0,36"/></svg>
  <h2 class="abs section-title deco">Our Services</h2>
  <div class="abs card" style="left:183px;top:155px">
    <div class="icon"><svg width="44" height="44" viewBox="0 0 44 44" fill="none" stroke="#111" stroke-width="2.5"><path d="M8 36 L26 18 M24 12 L34 22 L28 28 L18 18 Z"/><path d="M36 8 v6 M33 11 h6"/></svg></div>
    <h3>Janitorial<br>Services</h3>
    <p>Routine janitorial, Tall cleaning, Food service sanitation, Clean room services</p>
  </div>
  <div class="abs card" style="left:397px;top:183px">
    <div class="icon"><svg width="44" height="44" viewBox="0 0 44 44" fill="none" stroke="#111" stroke-width="2.5"><rect x="10" y="18" width="22" height="18" rx="2"/><path d="M16 18 V8 h14 M30 8 v6"/><circle cx="15" cy="38" r="2"/><circle cx="27" cy="38" r="2"/></svg></div>
    <h3>House Cleaning</h3>
    <p>Floors, Carpet cleaning, Refuse removal, Dusting, Interior windows, Blinds</p>
  </div>
  <div class="abs card" style="left:611px;top:155px">
    <div class="icon"><svg width="44" height="44" viewBox="0 0 44 44" fill="none" stroke="#111" stroke-width="2.5"><rect x="18" y="6" width="16" height="12" rx="1"/><path d="M22 18 L12 34 M26 18 L16 36"/></svg></div>
    <h3>Maintenance</h3>
    <p>Pressure washing, Gutters, Painting, Exterior windows, Construction cleanup, Detailing</p>
  </div>
  <div class="abs card" style="left:825px;top:183px">
    <div class="icon"><svg width="44" height="44" viewBox="0 0 44 44" fill="none" stroke="#111" stroke-width="2.5"><path d="M16 28 a10 10 0 1 1 12 0 v4 h-12 z"/><path d="M18 36 h8 M22 4 v3 M8 10 l2 2 M36 10 l-2 2"/></svg></div>
    <h3>Event<br>Services</h3>
    <p>Event hosting at the oak street studio Event cleanup</p>
  </div>
</section>

<section class="blogs">
  <svg class="edge" style="top:-22px" height="40" viewBox="0 0 1200 40" preserveAspectRatio="none"><polygon fill="#ebe5d9" points="0,24 90,12 170,28 260,14 340,26 430,10 520,24 600,12 690,28 780,14 860,26 950,10 1040,24 1120,14 1200,26 1200,40 0,40"/></svg>
  <h2 class="abs section-title deco">Our Blogs</h2>
  <article class="abs post" style="left:188px">
    <div class="post-photo" role="img" aria-label="Photo of a woman in a red shirt cleaning a kitchen" style="background:linear-gradient(135deg,#c9ccd0,#8f9398 60%,#b5403a)"></div>
    <span class="date">02 May 2018</span>
    <h4>Praesent elementum elit at tellus nec ultricies sit amet porttito</h4>
    <p>netus et malesuada fames ac turpis egestas Cras id elit integer quis urna Ut ante enim dapibus malesuada</p>
    <p class="more">Read More</p>
  </article>
  <article class="abs post" style="left:473px">
    <div class="post-photo" role="img" aria-label="Photo of a smiling woman wiping with a pink cloth" style="background:linear-gradient(135deg,#e9d6e0,#c77aa6 60%,#7fc4b8)"></div>
    <span class="date">02 May 2018</span>
    <h4>Praesent elementum elit at tellus nec ultricies sit amet porttito</h4>
    <p>netus et malesuada fames ac turpis egestas Cras id elit integer quis urna Ut ante enim dapibus malesuada</p>
    <p class="more">Read More</p>
  </article>
  <article class="abs post" style="left:758px">
    <div class="post-photo" role="img" aria-label="Photo of a worker cleaning a building exterior" style="background:linear-gradient(135deg,#eef0f2,#b9bec4 60%,#5d6670)"></div>
    <span class="date">02 May 2018</span>
    <h4>Praesent elementum elit at tellus nec ultricies sit amet porttito</h4>
    <p>netus et malesuada fames ac turpis egestas Cras id elit integer quis urna Ut ante enim dapibus malesuada</p>
    <p class="more">Read More</p>
  </article>
</section>

<section class="contact">
  <h2 class="abs section-title deco">Contact Us</h2>
  <p class="abs contact-intro">If you're ready to experience a professional cleaning, reach out to us now!</p>
  <div class="abs info" style="top:186px">
    <svg width="16" height="20" viewBox="0 0 16 20"><path d="M8 1a6 6 0 0 1 6 6c0 5-6 12-6 12S2 12 2 7a6 6 0 0 1 6-6z" fill="#111"/><circle cx="8" cy="7" r="2.2" fill="#f7e500"/></svg>
    <div><b>Address</b>418 SE Alder St #210, Portland, OR 97214</div>
  </div>
  <div class="abs info" style="top:254px">
    <svg width="16" height="18" viewBox="0 0 16 18" fill="none" stroke="#111" stroke-width="1.6"><path d="M3 2 l3 0 l1.5 4 l-2 1.5 a9 9 0 0 0 4 4 l1.5-2 l4 1.5 v3 a2 2 0 0 1-2 2 A13 13 0 0 1 1 4 a2 2 0 0 1 2-2z"/></svg>
    <div><b>Cell Phone</b>971-555-0148</div>
  </div>
  <div class="abs info" style="top:322px">
    <svg width="16" height="14" viewBox="0 0 16 14" fill="none" stroke="#111" stroke-width="1.6"><rect x="1" y="2" width="14" height="10"/><path d="M1 2 l7 6 l7-6"/></svg>
    <div><b>Email</b>hello@foxtrotlane.com</div>
  </div>
  <div class="abs field" style="left:550px;top:122px;width:230px">First Name</div>
  <div class="abs field" style="left:788px;top:122px;width:230px">Last Name</div>
  <div class="abs field" style="left:550px;top:168px;width:230px">Email</div>
  <div class="abs field" style="left:788px;top:168px;width:230px">Phone</div>
  <div class="abs field" style="left:550px;top:214px;width:468px;height:108px">Message</div>
  <div class="abs submit">Submit</div>
</section>

<footer class="footer">
  <svg class="edge" style="top:-30px" height="40" viewBox="0 0 1200 40" preserveAspectRatio="none"><polygon fill="#111111" points="0,20 40,10 90,24 140,8 190,22 240,12 300,26 350,10 410,24 460,8 520,22 580,12 640,26 700,10 760,24 820,8 880,22 940,12 1000,26 1060,10 1120,22 1200,12 1200,40 0,40"/></svg>
  <nav class="abs foot-nav"><a href="#">Home</a><a href="#">About Us</a><a href="#">Services</a><a href="#">Blogs</a><a href="#">Contact Us</a></nav>
  <p class="abs copy">© 2018 Company Name All right reserved</p>
  <div class="abs social"><span></span><span></span><span></span><span></span></div>
</footer>

</body>
</html>
```